US Recruiting Firm Needs Dynamic Tri-Fold Brochure

Need tri-fold professional brochure for HR recruiting and consulting firm based in the US.

Target Market(s)

Clients seeking administrative and human resources talent

Industry/Entity Type

Recruitment

Font styles to use
Sans Serif

Requirements
Should not have
• No weird shapes
• No heavy geometric shapes -- I prefer curvy lines
• Not a dark brochure

```html
<!DOCTYPE html>
<html lang="en">
<head>
<meta charset="utf-8">
<title>Piedmont Talent Partners – Tri-Fold Brochure</title>
<link rel="stylesheet" href="https://fonts.googleapis.com/css2?family=Open+Sans:ital,wght@0,400;0,600;0,700;0,800;1,600;1,700&display=swap">
<style>
:root{
  --navy:#1c3a5e;
  --navy-deep:#142c49;
  --orange:#e8661c;
  --orange-light:#f08a3e;
  --paper:#ffffff;
  --mist:#eef0f2;
  --ink:#3d4753;
  --muted:#6b7682;
  --stage:#e4e5e6;
}
*{box-sizing:border-box;margin:0;padding:0}
html,body{width:1200px;height:2400px;overflow:hidden;background:var(--stage)}
body{font-family:"Open Sans",Arial,sans-serif;color:var(--ink);position:relative}
.spread{position:absolute;left:0;width:1200px;height:927px;display:flex;box-shadow:0 6px 24px rgba(0,0,0,.12)}
.spread--outside{top:190px}
.spread--inside{top:1283px}
.panel{position:relative;width:400px;height:927px;overflow:hidden;background:var(--paper)}
.panel + .panel{border-left:1px solid rgba(0,0,0,.06)}
.shapes{position:absolute;inset:0;width:100%;height:100%}
.photo{position:absolute}
.layer{position:absolute;left:0;right:0}

/* outside left: positions */
.positions{background:linear-gradient(180deg,#f7f8f9 0%,var(--mist) 100%)}
.positions__intro{top:40px;padding:0 34px;font-weight:700;font-style:italic;font-size:17px;line-height:1.35;color:var(--navy);width:300px}
.positions__list{top:150px;padding:0 34px;list-style:none;font-size:13.5px;line-height:1.75;color:var(--muted)}
.positions__list li::before{content:"– "}
.badge{position:absolute;right:34px;top:175px;width:96px;height:96px;border-radius:50%;background:#fff;border:5px solid var(--mist);box-shadow:0 0 0 2px var(--navy)}

/* outside middle: services */
.services{background:var(--navy)}
.services__intro{top:40px;padding:0 32px;font-weight:700;font-style:italic;font-size:17px;line-height:1.35;color:var(--orange-light)}
.services__list{top:105px;padding:0 32px;list-style:none;font-size:13.5px;line-height:1.62;color:#fff}
.services__list li{padding-left:16px;position:relative}
.services__list li::before{content:"";position:absolute;left:0;top:8px;width:7px;height:7px;border-radius:50%;background:var(--orange)}
.contact__pill{position:absolute;left:60px;top:738px;width:280px;height:36px;border-radius:18px;background:var(--navy);color:#fff;font-weight:800;font-size:17px;letter-spacing:1px;text-align:center;line-height:36px}
.contact__body{top:786px;padding:0 40px;text-align:center;color:#fff;font-size:14px;line-height:1.5}
.contact__body strong{display:block;font-weight:700;font-style:italic}

/* outside right: cover */
.brand{position:absolute;top:52px;left:36px;right:20px;display:flex;align-items:center;gap:14px}
.brand__dot{width:50px;height:50px;border-radius:50%;background:var(--orange);flex:none}
.brand__name{font-weight:800;font-size:25px;line-height:1.08;color:var(--navy);text-transform:uppercase;letter-spacing:.5px}
.brand__tag{position:absolute;top:128px;left:100px;font-size:14px;font-weight:600;color:var(--navy)}
.cover__tagline{top:790px;padding:0 30px;font-weight:700;font-size:22px;line-height:1.3;color:#fff;text-transform:uppercase}

/* inside left: about */
.about__pill{position:absolute;left:28px;top:548px;padding:0 26px;height:34px;border-radius:17px;background:var(--orange);color:#fff;font-weight:800;font-size:18px;letter-spacing:.5px;line-height:34px}
.about__body{top:598px;padding:0 30px;color:#fff;font-size:12.5px;line-height:1.55}
.about__body p + p{margin-top:10px}

/* inside middle: partner */
.partner__title{top:38px;text-align:center;font-weight:800;font-size:19px;color:var(--navy)}
.partner__text{top:74px;padding:0 32px;font-size:12.5px;line-height:1.55;text-align:center}
.why__pill{position:absolute;left:60px;top:188px;width:280px;height:34px;border-radius:17px;background:var(--orange);color:#fff;font-weight:800;font-size:16px;text-align:center;line-height:34px;letter-spacing:.5px}
.why__intro{top:236px;padding:0 32px;font-size:12.5px;line-height:1.5}
.why__list{top:280px;padding:0 32px;list-style:none;font-size:13px;line-height:1.75}
.why__list li{display:flex;align-items:center;gap:9px}
.why__list svg{flex:none}
.mission__title{top:748px;text-align:center;font-weight:800;font-size:19px;color:var(--navy)}
.mission__text{top:782px;padding:0 30px;font-size:12.5px;line-height:1.55;text-align:center}

/* inside right: offers */
.offers{background:var(--paper)}
.offers__block{padding:0 30px}
.offers__head{font-weight:800;font-size:13.5px;color:var(--orange-light);text-transform:uppercase}
.offers__text{font-size:12.5px;line-height:1.45;color:#fff;margin-bottom:10px}
.offers__more{font-size:12.5px;line-height:1.5;color:#fff;margin-top:8px}
.cta{top:558px;text-align:center;padding:0 40px}
.cta__lead{font-weight:700;font-style:italic;font-size:14px;line-height:1.45;color:var(--orange)}
.cta__phone{margin-top:8px;display:inline-flex;align-items:center;gap:8px;font-weight:700;font-size:16px;color:var(--navy)}
</style>
</head>
<body>

<!-- OUTSIDE SPREAD -->
<section class="spread spread--outside">

  <article class="panel positions">
    <svg class="shapes" viewBox="0 0 400 927" preserveAspectRatio="none" aria-hidden="true">
      <path d="M0 690 Q200 640 400 700 V927 H0 Z" fill="#1c3a5e"/>
    </svg>
    <div class="photo" role="img" aria-label="Photo of business professionals walking through a bright office" style="left:0;top:724px;width:400px;height:203px;background:linear-gradient(180deg,#cfd6de,#8d99a6)"></div>
    <svg class="shapes" viewBox="0 0 400 927" preserveAspectRatio="none" aria-hidden="true">
      <path d="M0 700 Q200 660 400 712 V730 Q200 684 0 724 Z" fill="#1c3a5e"/>
    </svg>
    <p class="layer positions__intro">We offer stellar HR talent from entry to executive level. Positions that we fill include:</p>
    <ul class="layer positions__list">
      <li>HR Assistant</li><li>HR Coordinator</li><li>HR Specialist</li><li>HR Generalist</li>
      <li>HR Manager</li><li>HR Director</li><li>Benefits Administrator</li>
      <li>Talent Acquisition Specialist</li><li>Payroll Specialist</li><li>Recruiter</li>
      <li>HRIS Analyst</li><li>Compensation Analyst</li><li>Employee Relations Manager</li>
      <li>Training Specialist</li><li>Learning &amp; Development Consultant</li><li>Diversity &amp; Inclusion Consultant</li>
    </ul>
    <div class="badge" aria-hidden="true"></div>
  </article>

  <article class="panel services">
    <svg class="shapes" viewBox="0 0 400 927" preserveAspectRatio="none" aria-hidden="true">
      <path d="M0 640 Q200 720 400 650 V927 H0 Z" fill="#e8661c"/>
    </svg>
    <p class="layer services__intro">We provide customized recruiting and consulting services.</p>
    <ul class="layer services__list">
      <li>Working with hiring managers on requisitions</li>
      <li>Position &amp; Candidate Profiling</li>
      <li>Sourcing Resumes</li>
      <li>Writing and placing job postings</li>
      <li>Screening and interviewing candidates</li>
      <li>Shortlisting Candidates</li>
      <li>Conducting Assessments</li>
      <li>Coordinating Interviews &amp; Debriefing</li>
      <li>Candidate Dispositioning &amp; Updates</li>
      <li>Applicant Tracking</li>
      <li>Job Offers &amp; Salary Negotiation</li>
      <li>Start Date Coordination &amp; Offer Letter</li>
      <li>Onboarding Process &amp; New Hire Paperwork</li>
      <li>New Hire Follow-up &amp; Check-In Surveys</li>
    </ul>
    <div class="photo" role="img" aria-label="Circular photo of a smiling recruiter on the phone at her desk" style="left:140px;top:585px;width:120px;height:120px;border-radius:50%;border:4px solid #fff;background:radial-gradient(circle at 50% 40%,#f3e1cf,#7fa4c4)"></div>
    <div class="contact__pill">CONTACT US</div>
    <div class="layer contact__body">
      <strong>To learn more and request a FREE consultation, contact us today.</strong>
      Phone: 800-555-0142<br>Email: hello@piedmonttalent.com<br>Website: piedmonttalent.com
    </div>
  </article>

  <article class="panel cover">
    <div class="photo" role="img" aria-label="Photo of a confident professional woman with colleagues in a bright office" style="left:0;top:200px;width:400px;height:580px;background:linear-gradient(160deg,#e9eef3 0%,#b9c6d2 45%,#4d6278 100%)"></div>
    <svg class="shapes" viewBox="0 0 400 927" preserveAspectRatio="none" aria-hidden="true">
      <path d="M0 0 H400 V185 Q220 250 0 235 Z" fill="#ffffff"/>
      <path d="M0 235 Q220 250 400 185 V200 Q220 268 0 252 Z" fill="#1c3a5e"/>
      <path d="M0 252 Q220 268 400 200 V207 Q220 276 0 260 Z" fill="#e8661c"/>
      <path d="M0 770 Q200 700 400 735 V927 H0 Z" fill="#1c3a5e"/>
      <path d="M0 782 Q200 716 400 748 V927 H0 Z" fill="#e8661c"/>
    </svg>
    <div class="brand"><span class="brand__dot" aria-hidden="true"></span><span class="brand__name">Piedmont Talent Partners</span></div>
    <p class="brand__tag">Human Resources Staffing &amp; Consulting</p>
    <p class="layer cover__tagline">Specializing in administrative, professional, and executive HR talent</p>
  </article>
</section>

<!-- INSIDE SPREAD -->
<section class="spread spread--inside">

  <article class="panel about">
    <div class="photo" role="img" aria-label="Photo of a presenter leading a meeting with a seated team" style="left:0;top:0;width:400px;height:520px;background:linear-gradient(180deg,#f1f3f5,#b7c1cc)"></div>
    <svg class="shapes" viewBox="0 0 400 927" preserveAspectRatio="none" aria-hidden="true">
      <path d="M0 470 Q220 420 400 500 V927 H0 Z" fill="#e8661c"/>
      <path d="M0 490 Q220 440 400 520 V927 H0 Z" fill="#1c3a5e"/>
    </svg>
    <div class="about__pill">ABOUT US</div>
    <div class="layer about__body">
      <p>Piedmont Talent Partners is a recruiting and search firm that specializes in providing top-notch administrative, professional and executive level human resources talent. We provide best-in-class talent to companies seeking to simplify their recruiting process, increase efficiency and optimize productivity. Each search is customized to our clients' needs.</p>
      <p>At Piedmont Talent Partners, competence and integrity come first. We are experienced recruiters who understand the HR field. We take time to learn your culture, so every candidate we present is a strong fit and a lasting hire for your team.</p>
    </div>
  </article>

  <article class="panel partner">
    <h2 class="layer partner__title">A TRUSTED RECRUITING PARTNER</h2>
    <p class="layer partner__text">We have over 20 years of recruiting and human resources experience. Our recruiters know the hiring market and bring proven methods to every search, giving you a trusted partner.</p>
    <div class="why__pill">WHY CHOOSE US?</div>
    <p class="layer why__intro">We are HR experts dedicated to recruiting HR professionals.</p>
    <ul class="layer why__list">
      <li><svg width="14" height="14" viewBox="0 0 14 14"><circle cx="7" cy="7" r="7" fill="#e8661c"/><path d="M3.8 7.2l2.2 2.2 4.2-4.6" stroke="#fff" stroke-width="1.8" fill="none"/></svg>Highly qualified talent network</li>
      <li><svg width="14" height="14" viewBox="0 0 14 14"><circle cx="7" cy="7" r="7" fill="#e8661c"/><path d="M3.8 7.2l2.2 2.2 4.2-4.6" stroke="#fff" stroke-width="1.8" fill="none"/></svg>Comprehensive pre-screening</li>
      <li><svg width="14" height="14" viewBox="0 0 14 14"><circle cx="7" cy="7" r="7" fill="#e8661c"/><path d="M3.8 7.2l2.2 2.2 4.2-4.6" stroke="#fff" stroke-width="1.8" fill="none"/></svg>Streamlined recruiting process</li>
      <li><svg width="14" height="14" viewBox="0 0 14 14"><circle cx="7" cy="7" r="7" fill="#e8661c"/><path d="M3.8 7.2l2.2 2.2 4.2-4.6" stroke="#fff" stroke-width="1.8" fill="none"/></svg>Guaranteed placement fees</li>
      <li><svg width="14" height="14" viewBox="0 0 14 14"><circle cx="7" cy="7" r="7" fill="#e8661c"/><path d="M3.8 7.2l2.2 2.2 4.2-4.6" stroke="#fff" stroke-width="1.8" fill="none"/></svg>90-day replacement guarantee</li>
    </ul>
    <div class="photo" role="img" aria-label="Photo of colleagues reviewing documents at a desk with a keyboard" style="left:0;top:500px;width:400px;height:220px;background:linear-gradient(180deg,#f0f2f4,#c3ccd5)"></div>
    <svg class="shapes" viewBox="0 0 400 927" preserveAspectRatio="none" aria-hidden="true">
      <path d="M0 450 Q200 540 400 480 V505 Q200 560 0 480 Z" fill="#e8661c"/>
      <path d="M0 700 Q200 760 400 700 V727 Q200 775 0 727 Z" fill="#1c3a5e"/>
    </svg>
    <h2 class="layer mission__title">OUR MISSION</h2>
    <p class="layer mission__text">We have a two-fold mission: help companies hire the best HR talent to build stronger organizations, and help HR professionals find rewarding careers where their skills make a real impact.</p>
  </article>

  <article class="panel offers">
    <svg class="shapes" viewBox="0 0 400 927" preserveAspectRatio="none" aria-hidden="true">
      <path d="M0 0 H400 V470 Q180 560 0 500 Z" fill="#1c3a5e"/>
      <path d="M0 500 Q180 560 400 470 V482 Q180 574 0 512 Z" fill="#e8661c"/>
    </svg>
    <div class="layer offers__block" style="top:36px">
      <p class="offers__head">Contract Staffing</p>
      <p class="offers__text">One of the most critical functions in a company is finding the right people.</p>
      <p class="offers__head">Direct Hire</p>
      <p class="offers__text">Hire the candidate directly and see the impact right away.</p>
      <p class="offers__head">Consulting</p>
      <p class="offers__text">Step up by hiring the best human resources talent.</p>
      <p class="offers__more">Human resources professionals are no longer purely back-office roles. They shape culture, guide leaders and drive performance. We can help you hire HR talent that strengthens your company, whether you need one specialist or a full team that can advance your people strategy.</p>
    </div>
    <div class="layer cta">
      <p class="cta__lead">To learn more and request a FREE consultation, contact us today.</p>
      <p class="cta__phone"><svg width="18" height="18" viewBox="0 0 24 24"><path d="M6.6 10.8a15.1 15.1 0 006.6 6.6l2.2-2.2a1 1 0 011-.25 11.4 11.4 0 003.6.57 1 1 0 011 1V20a1 1 0 01-1 1A17 17 0 013 4a1 1 0 011-1h3.5a1 1 0 011 1c0 1.25.2 2.45.57 3.57a1 1 0 01-.25 1z" fill="#1c3a5e"/></svg>800-555-0142</p>
    </div>
    <div class="photo" role="img" aria-label="Photo of business people shaking hands across a meeting table" style="left:0;top:690px;width:400px;height:237px;background:linear-gradient(180deg,#dfe4ea,#7d8ea1)"></div>
    <svg class="shapes" viewBox="0 0 400 927" preserveAspectRatio="none" aria-hidden="true">
      <path d="M0 680 Q200 740 400 672 V700 Q200 760 0 705 Z" fill="#e8661c"/>
      <path d="M0 655 Q200 720 400 650 V672 Q200 740 0 680 Z" fill="#1c3a5e"/>
    </svg>
  </article>
</section>

</body>
</html>
```